Business card for a Exhibition booth fabrication company

Hi. My company would like to change our corporate name card. We are an events and Exhibition stand builder company. We would like our corporate name card to resonate what we do. I need someone to create something unique that relates to the industry that I am in. The graphic designer should be creative to incorporate the elements of my industry and try to blend in well in the design of the card. Our aim is to ensure that we are unique and our card can look different from our competitors.
Updates

Target Market(s)

Marketing and events manager from all companies

Contact Information for Business Card

The business card should have the following details:
Name
Job Title
Email
Website

Colors

Designer to choose colors to be used in the design.

Requirements
Must have
• The card must be look something that is relevant to the service that I am providing. My website is: www.velmora-buildworks.com
• You can see my website to get more information on what service that I am doing
Nice to have
• On the back of my card, I would like to have a globe image with the incorporation of my company logo. This is to indicate that my services can be done in any part of the world.

```html
<!DOCTYPE html>
<html lang="en">
<head>
<meta charset="utf-8">
<title>Velmora Buildworks — Business Card</title>
<link href="https://fonts.googleapis.com/css2?family=Arimo:wght@400;700&family=Open+Sans:wght@400&display=swap" rel="stylesheet">
<style>
  :root {
    --stage-light: #dcdcde;
    --stage-dark: #a4a5a8;
    --card-white: #ffffff;
    --brand-red: #ed1c24;
    --brand-grey: #636466;
    --wordmark-grey: #6d6e70;
    --silver: #d9dadc;
    --ink: #2b2b2b;
    --map-grey: #c9cacc;
  }
  * { margin: 0; padding: 0; box-sizing: border-box; }
  html, body { width: 1200px; height: 1118px; overflow: hidden; }
  body {
    position: relative;
    background: linear-gradient(90deg, var(--stage-light) 0%, #c4c5c8 45%, var(--stage-dark) 100%);
    font-family: "Open Sans", Arial, sans-serif;
  }
  .card {
    position: absolute;
    left: 223px;
    width: 754px;
    height: 430px;
    background: var(--card-white);
    overflow: hidden;
  }
  .card--front { top: 67px; border-radius: 9px; }
  .card--back { top: 566px; border-radius: 34px; }

  .front-band {
    position: absolute; left: 0; right: 0; top: 190px; bottom: 0;
    background: linear-gradient(90deg, var(--brand-red) 0%, var(--brand-red) 42%, var(--silver) 50%, var(--brand-grey) 58%, var(--brand-grey) 100%);
  }

  .brand { position: absolute; left: 376px; top: 40px; width: 346px; text-align: center; }
  .brand__mark {
    font-family: "Arimo", Arial, sans-serif;
    font-weight: 700;
    font-size: 40px;
    letter-spacing: 3px;
    color: var(--brand-red);
    line-height: 1;
  }
  .brand__wordmark {
    margin-top: 22px;
    font-family: "Arimo", Arial, sans-serif;
    font-size: 21px;
    letter-spacing: 2.4px;
    color: var(--wordmark-grey);
    white-space: nowrap;
  }

  .holder { position: absolute; left: 31px; top: 249px; color: var(--card-white); }
  .holder__name { font-family: "Arimo", Arial, sans-serif; font-weight: 700; font-size: 25px; letter-spacing: 0.6px; }
  .holder__title { font-family: "Arimo", Arial, sans-serif; font-size: 19px; margin-top: 4px; letter-spacing: 0.4px; }
  .holder__address { font-size: 17.5px; margin-top: 22px; line-height: 25px; }

  .contacts { position: absolute; right: 37px; top: 310px; list-style: none; color: var(--card-white); }
  .contacts li { display: flex; align-items: center; justify-content: flex-end; height: 34px; font-size: 17px; }
  .contacts svg { width: 20px; height: 20px; margin-left: 16px; }

  .globe-map {
    position: absolute; left: 46px; top: 50px; width: 667px; height: 200px;
    background: radial-gradient(ellipse at 50% 70%, #d6d7d9 0%, var(--map-grey) 40%, rgba(220,221,223,0.4) 72%, rgba(255,255,255,0) 100%);
    border-radius: 50% 50% 18% 18% / 90% 90% 20% 20%;
  }
  .floor-shadow {
    position: absolute; left: 80px; top: 332px; width: 600px; height: 50px;
    background: radial-gradient(ellipse at center, rgba(170,170,172,0.45) 0%, rgba(255,255,255,0) 70%);
  }
  .back-brand {
    position: absolute; left: 0; right: 0; top: 262px; text-align: center;
    font-family: "Arimo", Arial, sans-serif; font-weight: 700; font-size: 44px;
    letter-spacing: 3px; color: var(--brand-red);
  }
  .back-url {
    position: absolute; left: 0; right: 0; top: 392px; text-align: center;
    font-size: 21px; letter-spacing: 4.6px; color: var(--ink);
  }
</style>
</head>
<body>

<section class="card card--front">
  <div class="front-band" role="img" aria-label="Decorative red, silver and grey wave artwork sweeping across the lower card"></div>

  <div class="brand">
    <div class="brand__mark">VELMORA</div>
    <div class="brand__wordmark">VELMORA BUILDWORKS</div>
  </div>

  <div class="holder">
    <div class="holder__name">DARREN KELLAWAY</div>
    <div class="holder__title">PRESIDENT</div>
    <div class="holder__address">Street Name, City Name<br>Zipcode - 01234</div>
  </div>

  <ul class="contacts">
    <li>012-555-0147
      <svg viewBox="0 0 24 24" aria-hidden="true"><path fill="#fff" d="M6.6 10.8c1.4 2.8 3.8 5.1 6.6 6.6l2.2-2.2c.3-.3.7-.4 1-.2 1.1.4 2.3.6 3.6.6.6 0 1 .4 1 1V20c0 .6-.4 1-1 1C10.6 21 3 13.4 3 4c0-.6.4-1 1-1h3.5c.6 0 1 .4 1 1 0 1.3.2 2.5.6 3.6.1.3 0 .7-.2 1z"/></svg>
    </li>
    <li>info@velmora-buildworks.com
      <svg viewBox="0 0 24 24" aria-hidden="true"><rect x="2" y="5" width="20" height="14" fill="#fff"/><path d="M2 5l10 8 10-8M2 19l7.5-7M22 19l-7.5-7" stroke="#636466" stroke-width="1.4" fill="none"/></svg>
    </li>
    <li>www.velmora-buildworks.com
      <svg viewBox="0 0 24 24" aria-hidden="true"><g fill="none" stroke="#fff" stroke-width="1.6"><circle cx="12" cy="12" r="9.5"/><ellipse cx="12" cy="12" rx="4.2" ry="9.5"/><path d="M2.5 12h19M4 7h16M4 17h16M12 2.5v19"/></g></svg>
    </li>
  </ul>
</section>

<section class="card card--back">
  <div class="globe-map" role="img" aria-label="Soft grey world map arching across the card, showing worldwide service"></div>
  <div class="floor-shadow"></div>
  <div class="back-brand">VELMORA</div>
  <div class="back-url">www.velmora-buildworks.com</div>
</section>

</body>
</html>
```